"Full House" One Birchfield Circle- Our annual benefit is an evening of fun and fundraising.

We are non-profit organization that is looking for a good theme for our fundraiser in March 11, 2023. 5:30pm- 9:30PM. We have decided It is going to be a casino night, with fun at the tables, a shopping area, 50/50 raffle and raise a paddle . Our website is https://www.birchfieldcircle.org. We would like to see designs that have a festive theme that looks fun and not too flashy.

Target Market(s)

Ages 50+

Industry/Entity Type

Non-profit

Requirements
Nice to have
• A fun theme that is not so cheesy

```html
<!DOCTYPE html>
<html lang="en">
<head>
<meta charset="utf-8">
<title>Birchfield Circle Fundraiser Night</title>
<link rel="stylesheet" href="https://fonts.googleapis.com/css2?family=Red+Hat+Display:wght@400;500&family=Great+Vibes&family=Pacifico&family=Sacramento&family=Kaushan+Script&display=swap">
<style>
  :root {
    --ink: #222222;
    --muted: #555555;
    --paper: #ffffff;
    --night-dark: #0b0304;
    --deep-red: #4a0a10;
    --violet: #5a2e9c;
    --plum: #8f2f9f;
    --rose: #d6284e;
    --title-red: #d7222a;
    --venue: #7a1fa0;
    --chip-red: #e0262f;
    --bag-orange: #f2704c;
  }
  * { margin: 0; padding: 0; box-sizing: border-box; }
  html, body { width: 857px; height: 1200px; overflow: hidden; background: var(--paper); }
  .invite {
    position: relative; width: 857px; height: 1200px; overflow: hidden;
    font-family: "Red Hat Display", Arial, sans-serif; color: var(--ink);
  }
  .sign-photo {
    position: absolute; left: 0; top: 0; width: 333px; height: 1200px;
    background:
      radial-gradient(ellipse 120px 420px at 150px 620px, rgba(200,20,42,.85), rgba(90,10,18,.5) 60%, transparent 100%),
      linear-gradient(160deg, var(--night-dark) 0%, #1a0407 40%, var(--deep-red) 70%, #120204 100%);
  }
  .content { position: absolute; left: 333px; top: 0; width: 524px; height: 1200px; text-align: center; }
  .brand {
    position: absolute; top: 112px; left: 0; width: 100%;
    display: flex; align-items: center; justify-content: center; gap: 12px;
    font-size: 30px; font-weight: 500; line-height: 40px; color: var(--ink);
  }
  .brand-dot { width: 22px; height: 22px; border-radius: 50%; background: #5b7a2a; }
  .invite-line {
    position: absolute; top: 286px; left: 0; width: 100%;
    font-family: "Sacramento", cursive; font-size: 40px; line-height: 48px; color: var(--muted);
  }
  .title { position: absolute; top: 350px; left: 0; width: 100%; height: 200px; font-weight: 400; }
  .title-night {
    position: absolute; left: 0; top: 0; width: 100%; padding: 0 14px;
    font-family: "Great Vibes", cursive; font-size: 180px; line-height: 200px;
    background: linear-gradient(90deg, var(--violet), var(--plum) 50%, var(--rose));
    -webkit-background-clip: text; background-clip: text; color: transparent;
  }
  .title-fundraiser {
    position: absolute; left: 0; top: 22px; width: 100%;
    font-family: "Pacifico", cursive; font-size: 46px; line-height: 64px; color: var(--title-red);
    text-shadow: 2px 2px 0 #ffffff, 3px 3px 0 #444444;
  }
  .date { position: absolute; top: 584px; left: 0; width: 100%; font-size: 19px; line-height: 24px; color: var(--muted); }
  .time { position: absolute; top: 664px; left: 0; width: 100%; font-size: 19px; line-height: 24px; color: var(--muted); }
  .rule { position: absolute; left: 145px; width: 234px; height: 14px; }
  .rule-date { top: 631px; }
  .rule-venue { top: 1064px; }
  .features { position: absolute; top: 750px; left: 0; width: 100%; height: 140px; }
  .feature { position: absolute; top: 0; width: 150px; text-align: center; font-size: 19px; font-weight: 500; line-height: 24px; color: var(--ink); }
  .feature svg { display: block; margin: 0 auto 16px; }
  .f-casino { left: 15px; }
  .f-shop { left: 182px; }
  .f-auction { left: 342px; }
  .feature-divider { position: absolute; top: 42px; width: 1px; height: 100px; background: linear-gradient(var(--plum), var(--rose)); opacity: .7; }
  .d1 { left: 165px; }
  .d2 { left: 349px; }
  .venue { position: absolute; top: 962px; left: 0; width: 100%; font-family: "Kaushan Script", cursive; font-size: 38px; line-height: 50px; color: var(--venue); }
  .address { position: absolute; top: 1028px; left: 0; width: 100%; font-size: 18px; line-height: 24px; color: var(--ink); }
  .rsvp { position: absolute; top: 1102px; left: 0; width: 100%; font-size: 17px; line-height: 29px; color: var(--muted); letter-spacing: .3px; }
</style>
</head>
<body>
<main class="invite">
  <div class="sign-photo" role="img" aria-label="Night photograph of a vertical red neon casino sign"></div>
  <section class="content">
    <div class="brand"><span class="brand-dot"></span>Birchfield Circle</div>
    <p class="invite-line">you are invited to join our</p>
    <h1 class="title">
      <span class="title-night">Night</span>
      <span class="title-fundraiser">Fundraiser</span>
    </h1>
    <p class="date">Saturday, March 11, 2023</p>
    <svg class="rule rule-date" viewBox="0 0 234 14"><line x1="2" y1="7" x2="232" y2="7" stroke="#333" stroke-width="1.5"/><circle cx="3" cy="7" r="2" fill="#333"/><circle cx="231" cy="7" r="2" fill="#333"/><path d="M117 0 L122 7 L117 14 L112 7 Z" fill="#333"/></svg>
    <p class="time">5:30 pm - 9:30 pm</p>
    <div class="features">
      <div class="feature f-casino">
        <svg width="60" height="60" viewBox="0 0 60 60"><circle cx="30" cy="30" r="29" fill="var(--chip-red)"/><circle cx="30" cy="30" r="19" fill="#fff"/><circle cx="30" cy="30" r="13" fill="#333"/><path d="M30 22 C34 27 37 29 37 32 C37 35 33 36 31 34 L32 38 H28 L29 34 C27 36 23 35 23 32 C23 29 26 27 30 22 Z" fill="#fff"/></svg>
        Casino<br>Night
      </div>
      <div class="feature f-shop">
        <svg width="60" height="60" viewBox="0 0 60 60"><path d="M30 58 C18 44 8 36 8 24 A22 22 0 0 1 52 24 C52 36 42 44 30 58 Z" fill="var(--bag-orange)"/><rect x="19" y="20" width="22" height="20" rx="2" fill="#fff"/><path d="M25 20 V16 A5 5 0 0 1 35 16 V20" fill="none" stroke="#333" stroke-width="2"/></svg>
        Shopping<br>Area
      </div>
      <div class="feature f-auction">
        <svg width="60" height="60" viewBox="0 0 60 60"><rect x="27" y="28" width="6" height="28" rx="2" fill="#555"/><ellipse cx="30" cy="18" rx="14" ry="15" fill="#f0b89a" stroke="#333" stroke-width="2"/><text x="30" y="24" font-size="16" text-anchor="middle" fill="#333" font-family="Red Hat Display, sans-serif">$</text></svg>
        Silent<br>Auction
      </div>
      <span class="feature-divider d1"></span>
      <span class="feature-divider d2"></span>
    </div>
    <p class="venue">The Velvet Lounge</p>
    <p class="address">27 Linden Row, California 11208</p>
    <svg class="rule rule-venue" viewBox="0 0 234 14"><line x1="2" y1="7" x2="232" y2="7" stroke="#333" stroke-width="1.5"/><circle cx="3" cy="7" r="2.5" fill="#333"/><circle cx="231" cy="7" r="2.5" fill="#333"/><path d="M117 1 L123 7 L117 13 L111 7 Z" fill="#333"/><circle cx="105" cy="7" r="3" fill="#333"/><circle cx="129" cy="7" r="3" fill="#333"/></svg>
    <p class="rsvp">RSVP TO DANA WHITFIELD BEFORE 3RD MARCH, 2023<br>AT INFO@BIRCHFIELDCIRCLE.ORG</p>
  </section>
</main>
</body>
</html>
```